Business Card Design for company

We want new business cards. We'd like something different-- yet still highly professional. Our tagline is Guiding strategy, building results. Stock photos are ok, as long as they are relevant and look upscale.

Target Market(s)

Architecture/Business Management Consulting/Engineering Consulting

Contact Information for Business Card

dark gray background with pops of blue might be good, but you tell me. You're the designers. Rounded corners might be nice, but again, you tell me.

Font styles to use
Serif
Sans Serif

Colors
3276b5
5c5c5c
9d9d9d
fbfbfb

Requirements
Nice to have
• Something different, but still very professional.

```html
<!DOCTYPE html>
<html lang="en">
<head>
<meta charset="utf-8">
<title>Vantar Advisory – Business Cards</title>
<link href="https://fonts.googleapis.com/css2?family=Montserrat:wght@500;600&family=Open+Sans:wght@400&family=Arimo:wght@400&display=swap" rel="stylesheet">
<style>
  :root {
    --stage: #5e5e5e;
    --card-white: #ffffff;
    --brand-blue: #275f93;
    --accent-blue: #2a5d95;
    --ink-gray: #4a4c50;
    --text-gray: #4f4f4f;
    --rule-gray: #d8d8d8;
    --on-blue: #ffffff;
  }
  * { margin: 0; padding: 0; box-sizing: border-box; }
  html, body { width: 1200px; height: 802px; overflow: hidden; }
  body { background: var(--stage); position: relative; }

  .card {
    position: absolute;
    top: 274px;
    width: 443px;
    height: 265px;
    box-shadow: 2px 3px 6px rgba(0,0,0,0.45);
  }
  .card--front { left: 136px; background: var(--card-white); }
  .card--back  { left: 624px; background: var(--brand-blue); }

  .wordmark {
    position: absolute;
    font-family: "Montserrat", sans-serif;
    font-weight: 600;
    text-align: center;
    line-height: 1;
  }
  .wordmark__name { display: block; font-size: 38px; letter-spacing: 0; }
  .wordmark__sub  { display: block; font-size: 18px; letter-spacing: 4px; margin-top: 10px; padding-left: 4px; }
  .card--front .wordmark { left: 22px; top: 100px; width: 196px; color: var(--brand-blue); }
  .card--back .wordmark  { left: 0; top: 100px; width: 100%; color: var(--on-blue); }

  .divider {
    position: absolute;
    left: 224px; top: 58px;
    width: 1px; height: 142px;
    background: var(--rule-gray);
  }

  .contact { position: absolute; left: 237px; top: 67px; color: var(--text-gray); }
  .contact__name {
    font-family: "Montserrat", sans-serif;
    font-weight: 500;
    font-size: 16px;
    color: var(--ink-gray);
    line-height: 1;
  }
  .contact__name .first { color: var(--accent-blue); }
  .contact__title {
    font-family: "Arimo", sans-serif;
    font-size: 13px;
    line-height: 1;
    margin-top: 3px;
  }
  .contact__list { list-style: none; margin-top: 9px; }
  .contact__list li {
    font-family: "Arimo", sans-serif;
    font-size: 13px;
    height: 15.7px;
    line-height: 15.7px;
    display: flex;
    align-items: center;
    gap: 3px;
  }
  .contact__list svg { width: 10px; height: 10px; fill: var(--accent-blue); flex: none; }
  .contact__address {
    font-family: "Open Sans", sans-serif;
    font-size: 12.6px;
    line-height: 16px;
    margin-top: 5px;
    letter-spacing: 0.2px;
  }

  .tagline {
    position: absolute;
    left: 0; top: 223px;
    width: 100%;
    text-align: center;
    font-family: "Montserrat", sans-serif;
    font-weight: 600;
    font-size: 12.4px;
    color: var(--on-blue);
  }
</style>
</head>
<body>
  <section class="card card--front" aria-label="Business card front">
    <div class="wordmark">
      <span class="wordmark__name">VANTAR</span>
      <span class="wordmark__sub">ADVISORY</span>
    </div>
    <div class="divider"></div>
    <div class="contact">
      <p class="contact__name"><span class="first">DORIAN</span> HALE</p>
      <p class="contact__title">Managing Director</p>
      <ul class="contact__list">
        <li><svg viewBox="0 0 10 10" aria-hidden="true"><path d="M1 3.2C1 2 2.5 1.5 5 1.5S9 2 9 3.2v1H7V3.4H3v.8H1zM2.6 4.6h4.8L9 8.5H1z"/></svg>044-210 387 652</li>
        <li><svg viewBox="0 0 10 10" aria-hidden="true"><path d="M3 .5h4a.8.8 0 0 1 .8.8v7.4a.8.8 0 0 1-.8.8H3a.8.8 0 0 1-.8-.8V1.3A.8.8 0 0 1 3 .5zm.2 1.2v5.6h3.6V1.7z"/></svg>044-210 387 653</li>
        <li><svg viewBox="0 0 10 10" aria-hidden="true"><path d="M.8 2h8.4v6H.8zm.9.8L5 5.4l3.3-2.6z"/></svg>info@vantaradvisory.com</li>
        <li><svg viewBox="0 0 10 10" aria-hidden="true"><circle cx="5" cy="5" r="4.3"/></svg>www.vantaradvisory.com</li>
      </ul>
      <p class="contact__address">48 Larkspur Lane, Suite 7<br>Westbrook, 204519.</p>
    </div>
  </section>

  <section class="card card--back" aria-label="Business card back">
    <div class="wordmark">
      <span class="wordmark__name">VANTAR</span>
      <span class="wordmark__sub">ADVISORY</span>
    </div>
    <p class="tagline">GUIDING STRATEGY, BUILDING RESULTS</p>
  </section>
</body>
</html>
```